Oil and Gas Exploration and Production company needs a business card design

We need a business card design using our logo and colors in the logo. We want a mainstream design.

```html
<!DOCTYPE html>
<html lang="en">
<head>
<meta charset="utf-8">
<title>Solara Oil &amp; Gas – Business Card</title>
<link rel="stylesheet" href="https://fonts.googleapis.com/css2?family=Open+Sans:wght@400;700&display=swap">
<style>
  :root {
    --backdrop: #dcdcdc;
    --card: #ffffff;
    --ink: #1a1a1a;
    --crude: #231f20;
    --amber: #e09a1a;
    --tint: #fbfaf8;
  }
  html, body {
    margin: 0;
    padding: 0;
    width: 1200px;
    height: 942px;
    overflow: hidden;
    background: var(--backdrop);
    font-family: "Open Sans", sans-serif;
    color: var(--ink);
  }
  .canvas { position: relative; width: 1200px; height: 942px; }
  .card {
    position: absolute;
    left: 248px;
    width: 658px;
    height: 375px;
    background: var(--card);
    overflow: hidden;
  }
  .card--back { top: 78px; }
  .card--front { top: 486px; }

  .pattern-field {
    position: absolute;
    inset: 0;
    background: var(--tint);
  }
  .back-mark {
    position: absolute;
    left: 0; right: 0; top: 168px;
    display: flex;
    justify-content: center;
    align-items: center;
    gap: 12px;
  }
  .back-mark .name {
    font-weight: 700;
    font-size: 30px;
    line-height: 1.2;
    color: var(--crude);
  }
  .dot {
    display: inline-block;
    flex: none;
    border-radius: 50%;
    background: var(--amber);
  }
  .back-mark .dot { width: 22px; height: 22px; }

  .brand {
    position: absolute;
    left: 58px; top: 82px;
    display: flex;
    align-items: center;
    gap: 14px;
  }
  .brand .dot { width: 34px; height: 34px; }
  .brand .name {
    font-weight: 700;
    font-size: 42px;
    line-height: 1.1;
    color: var(--crude);
    white-space: nowrap;
  }

  .contacts {
    position: absolute;
    left: 60px; top: 213px;
    margin: 0; padding: 0;
    list-style: none;
    font-size: 16px;
  }
  .contacts li {
    display: flex;
    align-items: center;
    gap: 7px;
    height: 26.5px;
    white-space: nowrap;
  }
  .contacts svg { width: 15px; height: 15px; flex: none; }

  .person {
    position: absolute;
    right: 78px; top: 206px;
    text-align: right;
  }
  .person .full-name { font-size: 22px; line-height: 1.2; }
  .person .role { font-size: 16px; color: var(--amber); line-height: 1.2; }

  .band-amber {
    position: absolute; left: 0; right: 0; top: 357px; height: 6px;
    background: var(--amber);
  }
  .band-crude {
    position: absolute; left: 0; right: 0; top: 363px; height: 12px;
    background: #000;
  }
</style>
</head>
<body>
<div class="canvas">

  <section class="card card--back">
    <div class="pattern-field" role="img" aria-label="Faint repeated pattern across the card back"></div>
    <div class="back-mark">
      <span class="dot"></span>
      <span class="name">Solara Oil &amp; Gas</span>
    </div>
  </section>

  <section class="card card--front">
    <div class="brand">
      <span class="dot"></span>
      <span class="name">Solara Oil &amp; Gas</span>
    </div>

    <ul class="contacts">
      <li>
        <svg viewBox="0 0 16 16" aria-hidden="true"><rect width="16" height="16" rx="2" fill="#e09a1a"/><rect x="4" y="3" width="8" height="3" fill="#fff"/><rect x="3" y="7" width="10" height="4" fill="#fff"/><rect x="5" y="10" width="6" height="3" fill="#fff"/></svg>
        <span>1 555-210-4836</span>
      </li>
      <li>
        <svg viewBox="0 0 16 16" aria-hidden="true"><rect width="16" height="16" rx="2" fill="#e09a1a"/><path d="M5 3.5 L7 3.5 L7.5 6 L6.3 6.8 Q7.3 9 9.2 9.7 L10 8.5 L12.5 9 L12.5 11 Q12 12.5 10.5 12.5 Q4 11.5 3.5 5 Q3.5 3.5 5 3.5 Z" fill="#fff"/></svg>
        <span>+1 555-210-0092</span>
      </li>
      <li>
        <svg viewBox="0 0 16 16" aria-hidden="true"><rect width="16" height="16" rx="2" fill="#e09a1a"/><rect x="3" y="4.5" width="10" height="7" fill="none" stroke="#fff" stroke-width="1.2"/><path d="M3 4.5 L8 8.5 L13 4.5" fill="none" stroke="#fff" stroke-width="1.2"/></svg>
        <span>info@solaraoilgas.com</span>
      </li>
      <li>
        <svg viewBox="0 0 16 16" aria-hidden="true"><rect width="16" height="16" rx="2" fill="#e09a1a"/><path d="M8 13 Q4 8.5 4 6.5 A4 4 0 0 1 12 6.5 Q12 8.5 8 13 Z" fill="#fff"/><circle cx="8" cy="6.5" r="1.5" fill="#e09a1a"/></svg>
        <span>PO Box 4120, Sample Street, Fort Worth, TX 76101-4120, USA</span>
      </li>
    </ul>

    <div class="person">
      <div class="full-name">Dale Harmon</div>
      <div class="role">CEO</div>
    </div>

    <div class="band-amber"></div>
    <div class="band-crude"></div>
  </section>

</div>
</body>
</html>
```